zorvan lumet website design

An IT support and IT Security Company - just use dummy text for now for the design. Examples of sites we like the looks and feel of but need it more professional feel are like: www.kelbrovault.uk.com , www.pravok.co.uk, www.quenthardy.com/professional/, www.vur.com, www.melvish.com,

Best to message me if you have any questions

Target Market(s)

small to medium UK based companies that require IT support services

Industry/Entity Type

It Company

Contact Information for Business Card

use dummy name, telephone and email for now, will provide details later.

Logo Text

zorvan lumet (and then below the logo it should say "your IT, networks and security partner")

Coding

Coded - Design and coding required

Number of Pages Required

5+ page

Colors

Designer to choose colors to be used in the design.

Requirements
Must have
• must be professional, yet simple and clear that this is a serious IT support and IT security company.
Nice to have
• 1)The website homepage must have professional quality pictures of IT support or London city skyline or any picture that projects friendly business partners, professionalism and ready to serve.
• 2) Home page needs to include tabs for following pages 'Services' , 'About Us' , 'Contact Us' 'Home'
• 3) Website built customised using wordpress is ideal and easy for us to manage.
• more room for boxed options from homepage (with pic or image in background)
Should not have
• no checkout trolleys or payment options.

```html
<!DOCTYPE html>
<html lang="en">
<head>
<meta charset="utf-8">
<title>zorvan lumet – IT Support &amp; IT Security</title>
<link rel="stylesheet" href="https://fonts.googleapis.com/css2?family=Archivo+Black&family=Open+Sans:ital,wght@0,400;0,600;0,700;1,400&display=swap">
<style>
  :root {
    --brand: #29a9cf;
    --brand-light: #7fcbe2;
    --ink: #333333;
    --text: #555555;
    --muted: #6a6a6a;
    --white: #ffffff;
    --footer: #333333;
    --hero-top: #d9dee5;
    --hero-bottom: #c9ced4;
    --office-light: #e4eef4;
    --office-mid: #c9dbe6;
  }
  * { box-sizing: border-box; margin: 0; padding: 0; }
  html, body { width: 667px; height: 1200px; overflow: hidden; }
  body { position: relative; background: var(--white); font-family: "Open Sans", Arial, sans-serif; color: var(--text); }

  .site-header { position: absolute; left: 0; top: 0; width: 667px; height: 64px; border-top: 3px solid var(--brand); background: var(--white); }
  .brand { position: absolute; left: 45px; top: 15px; font-weight: 700; font-size: 24px; color: var(--brand); letter-spacing: 0.2px; }
  .main-nav { position: absolute; left: 409px; top: -3px; height: 64px; display: flex; }
  .main-nav a { display: flex; align-items: center; height: 64px; padding: 0 8px; font-size: 9.6px; color: var(--ink); text-decoration: none; margin-right: 5px; }
  .main-nav a.is-active { background: var(--brand); color: var(--white); margin-right: 6px; width: 43px; justify-content: center; padding: 0; }

  .hero { position: absolute; left: 0; top: 64px; width: 667px; height: 312px; text-align: center; }
  .hero-image { position: absolute; inset: 0; background: linear-gradient(180deg, var(--hero-top) 0%, #d3d9e0 55%, var(--hero-bottom) 100%); }
  .hero-title { position: absolute; left: 0; width: 667px; top: 115px; font-family: "Archivo Black", Arial, sans-serif; font-size: 23px; color: var(--ink); }
  .hero-lead { position: absolute; left: 116px; width: 435px; top: 158px; font-size: 9.4px; line-height: 16px; color: var(--ink); }

  .welcome { position: absolute; left: 0; top: 376px; width: 667px; height: 174px; text-align: center; }
  .section-title { font-family: "Archivo Black", Arial, sans-serif; font-size: 21px; color: var(--brand); }
  .welcome .section-title { position: absolute; top: 27px; width: 667px; }
  .welcome-text { position: absolute; left: 118px; width: 431px; top: 59px; font-size: 8.6px; line-height: 14px; color: var(--muted); }
  .welcome-text p + p { margin-top: 9px; }

  .services { position: absolute; left: 0; top: 550px; width: 667px; height: 267px; }
  .services-backdrop { position: absolute; inset: 0; background: linear-gradient(90deg, var(--office-mid) 0%, var(--office-light) 45%, #dbe8ef 100%); }
  .services-portrait { position: absolute; left: 11px; top: 5px; width: 237px; height: 262px; background: linear-gradient(180deg, #9aa7b3 0%, #3a4255 55%, #262c3b 100%); border-radius: 90px 90px 0 0; }
  .services .heading { position: absolute; left: 214px; width: 410px; top: 49px; text-align: center; font-family: "Archivo Black", Arial, sans-serif; font-size: 24px; color: var(--ink); }
  .service-card { position: absolute; top: 100px; width: 197px; height: 117px; background: var(--white); border: 1px solid #cfd6da; }
  .service-card.security { left: 214px; }
  .service-card.support { left: 427px; }
  .service-icon { position: absolute; left: 8px; top: 27px; width: 24px; height: 22px; }
  .service-name { position: absolute; left: 40px; top: 22px; font-size: 13px; font-weight: 600; color: var(--text); }
  .service-text { position: absolute; left: 40px; top: 43px; width: 120px; font-size: 8.6px; line-height: 14px; color: var(--text); }
  .read-more { position: absolute; right: -1px; top: -1px; width: 26px; height: 117px; background: var(--brand); color: var(--white); font-size: 10px; font-weight: 700; writing-mode: vertical-rl; transform: rotate(180deg); display: flex; align-items: center; justify-content: center; letter-spacing: 0.4px; }

  .testimonials { position: absolute; left: 0; top: 817px; width: 667px; height: 191px; }
  .testimonials .section-title { position: absolute; top: 23px; width: 667px; text-align: center; }
  .testimonial { position: absolute; top: 66px; width: 266px; }
  .testimonial.first { left: 45px; }
  .testimonial.second { left: 347px; }
  .client-name { font-size: 12px; font-weight: 600; color: var(--text); }
  .client-quote { margin-top: 5px; font-size: 8.2px; line-height: 14px; font-style: italic; color: var(--muted); }
  .slider-dots { position: absolute; left: 301px; top: 154px; display: flex; gap: 4px; }
  .slider-dots span { width: 19px; height: 2px; background: #8a8a8a; }
  .slider-dots span.is-active { background: var(--brand); }

  .contact { position: absolute; left: 0; top: 1008px; width: 667px; height: 162px; background: var(--brand); }
  .field { position: absolute; background: var(--brand-light); color: var(--white); font-size: 8.6px; padding: 6px 12px; border-radius: 2px; }
  .field.name { left: 125px; top: 43px; width: 202px; height: 23px; }
  .field.email { left: 125px; top: 72px; width: 202px; height: 23px; }
  .field.phone { left: 125px; top: 101px; width: 202px; height: 23px; }
  .field.message { left: 339px; top: 43px; width: 203px; height: 52px; }
  .submit { position: absolute; left: 339px; top: 101px; width: 203px; height: 23px; background: var(--white); color: var(--brand); font-size: 11px; font-weight: 700; display: flex; align-items: center; justify-content: center; border-radius: 2px; letter-spacing: 0.3px; }

  .site-footer { position: absolute; left: 0; top: 1170px; width: 667px; height: 30px; background: var(--footer); color: #e6e6e6; font-size: 8.8px; display: flex; align-items: center; justify-content: center; }
</style>
</head>
<body>
  <header class="site-header">
    <div class="brand">zorvan lumet</div>
    <nav class="main-nav">
      <a class="is-active" href="#">HOME</a>
      <a href="#">ABOUT</a>
      <a href="#">SERVICES</a>
      <a href="#">CONTACT</a>
    </nav>
  </header>

  <section class="hero">
    <div class="hero-image" role="img" aria-label="Pale photo of the London city skyline with office towers"></div>
    <h1 class="hero-title">Lorem Ipsum is simply dummy text.</h1>
    <p class="hero-lead">Lorem Ipsum is simply dummy text of the printing and typesetting industry. Lorem Ipsum has been the industry's standard dummy text ever since the 1500s, when an unknown printer took a galley of type and scrambled it to make a type specimen book.</p>
  </section>

  <section class="welcome">
    <h2 class="section-title">Welcome to zorvan lumet</h2>
    <div class="welcome-text">
      <p>Lorem Ipsum is simply dummy text of the printing and typesetting industry. Lorem Ipsum has been the industry's standard dummy text ever since the 1500s, when an unknown printer took a galley of type and scrambled it to make a type specimen book.</p>
      <p>It has survived not only five centuries, but also the leap into electronic typesetting, remaining essentially unchanged. It was popularised in the 1960s with the release of Quillmark sheets containing Lorem Ipsum.</p>
    </div>
  </section>

  <section class="services">
    <div class="services-backdrop" role="img" aria-label="Soft blurred bright office interior"></div>
    <div class="services-portrait" role="img" aria-label="Photo of a smiling businessman in a suit holding a tablet"></div>
    <h2 class="heading">Our Services</h2>

    <article class="service-card security">
      <svg class="service-icon" viewBox="0 0 24 22" aria-hidden="true">
        <rect x="1" y="1" width="22" height="14" rx="1" fill="none" stroke="var(--brand)" stroke-width="2"/>
        <rect x="9" y="15" width="6" height="3" fill="var(--brand)"/>
        <rect x="6" y="18" width="12" height="2" fill="var(--brand)"/>
        <rect x="9" y="7" width="6" height="5" fill="var(--brand)"/>
        <path d="M10 7 V5.5 a2 2 0 0 1 4 0 V7" fill="none" stroke="var(--brand)" stroke-width="1.2"/>
      </svg>
      <h3 class="service-name">IT security</h3>
      <p class="service-text">Lorem ipsum dolor sit amet, consectetur adipiscing elit. Etiam fringilla odio in mollis tincidunt per mauris.</p>
      <div class="read-more">READ MORE</div>
    </article>

    <article class="service-card support">
      <svg class="service-icon" viewBox="0 0 24 22" aria-hidden="true">
        <rect x="1" y="3" width="22" height="12" rx="1" fill="none" stroke="var(--brand)" stroke-width="2"/>
        <rect x="9" y="15" width="6" height="3" fill="var(--brand)"/>
        <rect x="6" y="18" width="12" height="2" fill="var(--brand)"/>
        <circle cx="12" cy="9" r="3" fill="none" stroke="var(--brand)" stroke-width="2"/>
        <circle cx="5" cy="7" r="1.3" fill="var(--brand)"/>
        <circle cx="19" cy="11" r="1.3" fill="var(--brand)"/>
      </svg>
      <h3 class="service-name">IT support</h3>
      <p class="service-text">Lorem ipsum dolor sit amet, consectetur adipiscing elit. Etiam fringilla odio in mollis tincidunt per mauris.</p>
      <div class="read-more">READ MORE</div>
    </article>
  </section>

  <section class="testimonials">
    <h2 class="section-title">Client Testimonials</h2>
    <blockquote class="testimonial first">
      <p class="client-name">- Client Name</p>
      <p class="client-quote">Lorem Ipsum is simply dummy text of the printing and typesetting industry. Lorem Ipsum has been the industry's standard dummy text ever since the 1500s, when an unknown printer took a galley of type.</p>
    </blockquote>
    <blockquote class="testimonial second">
      <p class="client-name">- Client Name</p>
      <p class="client-quote">Lorem Ipsum is simply dummy text of the printing and typesetting industry. Lorem Ipsum has been the industry's standard dummy text ever since the 1500s, when an unknown printer took a galley of type.</p>
    </blockquote>
    <div class="slider-dots"><span class="is-active"></span><span></span><span></span></div>
  </section>

  <section class="contact">
    <div class="field name">Name</div>
    <div class="field email">Email</div>
    <div class="field phone">Phone</div>
    <div class="field message">Message</div>
    <div class="submit">SUBMIT</div>
  </section>

  <footer class="site-footer">2018 ©zorvanlumet- All Rights Reserved.</footer>
</body>
</html>
```